The Vellmark Company Sweet Packaging Design

The Vellmark Goods Company is looking for a logo and label design for an upcoming line of honey based health and beauty products that are sourced from the Polynesian Islands (Hawaii, New Zealand, Fiji etc.).The brand will be premium price positioned and the design and packaging should exude class and quality.The design should be flexible enough to add products from future locations.We would like to see the design across three different product forms:1. Glass Honey Jar (main product)2. Hand cream / lotion (pump bottle, or lotion tube)3. Small box (e.g. throat lozenges / gum packet etc.)The Polynesia Islands are unique and exotic locations; the design/packaging should reflect this but should not be overly complicated. Each individual island has their own distinct culture and history but they have many commonalities which fall under "Polynesian Culture". The Vellmark Goods Company is an umbrella brand that should be able to support a growing number of products.Possible designs may (but are not required to) incorporate local flowers (Hawaii / Hibiscus flower, New Zealand / Manuka Flower etc.) into the design, Islands, and boutique feel (elegant classy looking)Please feel free to ask more questions for further guidance but we really want to see where the creative process can take us outside of what we have already considered internally.
Updates

We needed to modify our idea slightly because of competition.

We needed extend to get a few more ideas. We did not want to copy our competition and needed to add a part to our design that we did not include before.

Target Market(s)

Health conscious people. Honey lovers.

Font styles to use
Serif
Sans Serif
Decorative

Colors

Designer to choose colors to be used in the design.

Requirements
Must have
• a little tribal look. because its 100% island honey.. it would be nice to have the fee of that in the design..

```html
<!DOCTYPE html>
<html lang="en">
<head>
<meta charset="utf-8">
<title>Packaging Series – Proposition 1</title>
<link rel="stylesheet" href="https://fonts.googleapis.com/css2?family=Karla:wght@400;500&family=Playfair+Display:wght@800;900&display=swap">
<style>
  :root {
    --green: #3ab54a;
    --yellow: #fadc2f;
    --ink: #111111;
    --paper: #ffffff;
    --edge: #3a3a3a;
    --sans: "Karla", "Helvetica Neue", Arial, sans-serif;
    --serif: "Playfair Display", Georgia, serif;
  }
  * { margin: 0; padding: 0; box-sizing: border-box; }
  html, body { width: 1200px; height: 1200px; overflow: hidden; background: var(--paper); }
  .canvas { position: relative; width: 1200px; height: 1200px; font-family: var(--sans); color: var(--ink); }

  .heading { position: absolute; left: 59px; color: var(--green); font-weight: 400; line-height: 1; }
  .heading--series { top: 55px; font-size: 47px; letter-spacing: 0.09em; }
  .heading--proposition { top: 111px; font-size: 49px; letter-spacing: 0.06em; }
  .intro { position: absolute; left: 58px; top: 189px; font-size: 22px; line-height: 29px; color: var(--green); letter-spacing: 0.1em; }

  .label { position: absolute; background: var(--paper); border: 1px solid var(--edge); overflow: hidden; }
  .label--cream { left: 59px; top: 317px; width: 322px; height: 681px; }
  .label--lozenges { left: 406px; top: 316px; width: 629px; height: 382px; }
  .label--jar { left: 406px; top: 728px; width: 742px; height: 425px; }

  .band { position: absolute; left: 0; right: 0; background: var(--yellow); }
  .label--cream .band--top { top: 0; height: 228px; }
  .label--cream .band--bottom { top: 567px; bottom: 0; }
  .label--lozenges .band--top { top: 0; height: 190px; }
  .label--lozenges .band--bottom { top: 328px; bottom: 0; }
  .label--jar .band--top { top: 0; height: 188px; }
  .label--jar .band--bottom { top: 372px; bottom: 0; }

  .line { position: absolute; left: 0; right: 0; text-align: center; white-space: nowrap; }
  .brand-mark { position: absolute; left: 50%; transform: translateX(-50%); display: block; }
  .brand-name { text-transform: uppercase; letter-spacing: 0.1em; font-weight: 500; }
  .variety { font-weight: 400; letter-spacing: 0.03em; }
  .product { font-family: var(--serif); font-weight: 900; font-variant-numeric: lining-nums; }
  .benefit { font-weight: 400; letter-spacing: 0.04em; }
  .volume { font-family: var(--serif); font-weight: 800; font-variant-numeric: lining-nums; }
  .origin-note { font-weight: 400; }

  .label--cream .brand-mark { top: 27px; }
  .label--cream .brand-name { top: 150px; font-size: 20px; line-height: 27px; }
  .label--cream .variety { top: 331px; font-size: 24px; line-height: 30px; }
  .label--cream .product { top: 363px; font-size: 42px; line-height: 50px; }
  .label--cream .benefit { top: 428px; font-size: 24px; line-height: 30px; }
  .label--cream .origin-note { top: 604px; font-size: 17px; line-height: 20px; }
  .label--cream .volume { top: 637px; font-size: 19px; line-height: 22px; }

  .label--lozenges .brand-mark { top: 29px; }
  .label--lozenges .brand-name { top: 124px; font-size: 16px; line-height: 21px; }
  .label--lozenges .variety { top: 210px; font-size: 19px; line-height: 24px; }
  .label--lozenges .product { top: 235px; font-size: 34px; line-height: 40px; }
  .label--lozenges .benefit { top: 285px; font-size: 19px; line-height: 24px; }
  .label--lozenges .volume { top: 339px; font-size: 19px; line-height: 24px; }

  .label--jar .brand-mark { top: 27px; }
  .label--jar .brand-name { top: 122px; font-size: 16px; line-height: 21px; }
  .label--jar .variety { top: 217px; font-size: 24px; line-height: 30px; }
  .label--jar .product { top: 250px; font-size: 43px; line-height: 50px; }
  .label--jar .benefit { top: 314px; font-size: 24px; line-height: 30px; }
  .label--jar .volume { top: 384px; font-size: 19px; line-height: 24px; }
</style>
</head>
<body>
<main class="canvas">
  <h1 class="heading heading--series">PACKAGING SERIES</h1>
  <h2 class="heading heading--proposition">Proposition 1</h2>
  <p class="intro">Minimalistic white, black and yellow labels with central<br>design. Logo will be replaced with the version of your choice.</p>

  <section class="label label--cream">
    <div class="band band--top"></div>
    <svg class="brand-mark" width="112" height="112" viewBox="0 0 112 112" aria-hidden="true"><circle cx="56" cy="56" r="53" fill="none" stroke="var(--ink)" stroke-width="3"/></svg>
    <p class="line brand-name">The Vellmark<br>Goods Company</p>
    <p class="line variety">Manuka Honey</p>
    <p class="line product">Hand Cream</p>
    <p class="line benefit">Moisturizing</p>
    <div class="band band--bottom"></div>
    <p class="line origin-note">Made from 100% pure island honey.</p>
    <p class="line volume">125 ml | 4.25 fl oz.</p>
  </section>

  <section class="label label--lozenges">
    <div class="band band--top"></div>
    <svg class="brand-mark" width="88" height="88" viewBox="0 0 88 88" aria-hidden="true"><circle cx="44" cy="44" r="41.5" fill="none" stroke="var(--ink)" stroke-width="2.5"/></svg>
    <p class="line brand-name">The Vellmark<br>Goods Company</p>
    <p class="line variety">Hibiscus Honey</p>
    <p class="line product">Throat Lozenges</p>
    <p class="line benefit">Antibacterial</p>
    <div class="band band--bottom"></div>
    <p class="line volume">16 Lozenges</p>
  </section>

  <section class="label label--jar">
    <div class="band band--top"></div>
    <svg class="brand-mark" width="88" height="88" viewBox="0 0 88 88" aria-hidden="true"><circle cx="44" cy="44" r="41.5" fill="none" stroke="var(--ink)" stroke-width="2.5"/></svg>
    <p class="line brand-name">The Vellmark<br>Goods Company</p>
    <p class="line variety">Manuka Blossom</p>
    <p class="line product">Honey</p>
    <p class="line benefit">New Zealand</p>
    <div class="band band--bottom"></div>
    <p class="line volume">250 ml | 8.45 fl oz.</p>
  </section>
</main>
</body>
</html>
```